Computer Company needs a Business card design

We need a business card design for our business. We assist people to transition to the KVS (Kestrel Vantage Scheme). The Verandal Crown Office-owned kvs™ network is a brand new telecommunications network currently being rolled out across Australia, giving access to a reliable broadband connection. Our niche market will predominantly be domestic customers in the 50+ age bracket. The assistance that we provide is everything from arranging the equipment, arranging the plan and contract term, appointment times, final testing of the network and any tweaks that need to be made. We basically PM the transition from start to finish. The business card design should be minimalist, should communicate loyalty and stability, should be easy to read and clearly explain what we do. We have asked for front and back. However, the back of the card does not have to include much information at all. It could be just a small design, or a repeat of our phone number. Up to you. The attached file only says what is required on the card. It does not specify where to arrange the text, what fonts to use, etc etc. As much as we would like to give you more info, due to our very limited design ability, we are not really able to send you any rough, or otherwise, designs of what we are after. Hopefully the above description is enough for you.

```html
<!DOCTYPE html>
<html lang="en">
<head>
<meta charset="utf-8">
<title>Tidewell Connect – Business Card</title>
<link rel="stylesheet" href="https://fonts.googleapis.com/css2?family=Lato:wght@400;700&display=swap">
<style>
  :root {
    --backdrop: #2e2e30;
    --brand-blue: #1f57ad;
    --deep-blue: #2a4a9c;
    --glow-blue: #0b7fd0;
    --swoosh-blue: #1b8fd6;
    --paper: #ffffff;
  }
  * { box-sizing: border-box; margin: 0; padding: 0; }
  html, body {
    width: 1200px; height: 900px; overflow: hidden;
    background: var(--backdrop);
    font-family: "Lato", Arial, sans-serif;
  }
  .sheet { position: relative; width: 1200px; height: 900px; }
  .card {
    position: absolute; width: 620px; height: 354px; overflow: hidden;
    box-shadow: 0 10px 24px rgba(0,0,0,.45);
  }
  /* Back of card */
  .card--back {
    left: 290px; top: 50px;
    background: radial-gradient(ellipse at 50% 40%, var(--glow-blue) 0%, #0760b4 45%, var(--deep-blue) 100%);
    color: var(--paper);
  }
  .brand {
    position: absolute; display: flex; align-items: center; gap: 18px;
    font-weight: 700; letter-spacing: .5px; white-space: nowrap;
  }
  .card--back .brand {
    left: 50%; top: 120px; transform: translateX(-50%);
    font-size: 48px;
  }
  .brand__dot { display: block; border-radius: 50%; flex: none; }
  .card--back .brand__dot { width: 70px; height: 70px; background: var(--paper); }
  .web-line {
    position: absolute; left: 0; right: 0; top: 262px; text-align: center;
    font-size: 15px; letter-spacing: 2px;
  }
  /* Front of card */
  .card--front { left: 290px; top: 486px; background: var(--paper); }
  .card__shape { position: absolute; inset: 0; width: 100%; height: 100%; }
  .card--front .brand {
    left: 40px; top: 52px; font-size: 44px; color: var(--brand-blue);
  }
  .card--front .brand__dot { width: 74px; height: 74px; background: var(--brand-blue); }
  .address {
    position: absolute; left: 40px; top: 268px;
    color: var(--paper); font-size: 18px; font-style: normal; line-height: 1.35;
  }
  .contact {
    position: absolute; right: 34px; top: 222px; text-align: right;
    color: var(--paper);
  }
  .contact__name { font-size: 25px; font-weight: 700; margin-bottom: 12px; }
  .contact__row {
    display: flex; justify-content: flex-end; align-items: center; gap: 10px;
    font-size: 16px; line-height: 1.5;
  }
  .contact__icon { width: 15px; height: 15px; flex: none; }
</style>
</head>
<body>
<main class="sheet">

  <section class="card card--back" aria-label="Back of business card">
    <div class="brand">
      <span class="brand__name">Tidewell Connect</span>
      <span class="brand__dot" aria-hidden="true"></span>
    </div>
    <p class="web-line">www.tidewellconnect.com.au</p>
  </section>

  <section class="card card--front" aria-label="Front of business card">
    <svg class="card__shape" viewBox="0 0 620 354" preserveAspectRatio="none" aria-hidden="true">
      <defs>
        <radialGradient id="band-fill" cx="70%" cy="75%" r="70%">
          <stop offset="0%" stop-color="#0b7fd0"/>
          <stop offset="55%" stop-color="#0d63b8"/>
          <stop offset="100%" stop-color="#2a4a9c"/>
        </radialGradient>
      </defs>
      <path d="M0,236 Q330,290 585,0 L620,0 L620,354 L0,354 Z" fill="url(#band-fill)"/>
      <path d="M250,272 Q470,250 590,0 L612,0 Q470,272 250,272 Z" fill="#1b8fd6"/>
    </svg>

    <div class="brand">
      <span class="brand__name">Tidewell Connect</span>
      <span class="brand__dot" aria-hidden="true"></span>
    </div>

    <address class="address">
      2150 Harlow Lane<br>
      Westbury TX 78000
    </address>

    <div class="contact">
      <p class="contact__name">Reid Ashcombe</p>
      <p class="contact__row">042 518 7730
        <svg class="contact__icon" viewBox="0 0 16 16" aria-hidden="true"><path fill="#fff" d="M3.5 1 6 4 4.6 5.6a9 9 0 0 0 5.8 5.8L12 10l3 2.5-1.6 2.3C7.5 15 1 8.5 1.2 2.6Z"/></svg>
      </p>
      <p class="contact__row">info@tidewellconnect.com.au
        <svg class="contact__icon" viewBox="0 0 16 16" aria-hidden="true"><rect x="1" y="3" width="14" height="10" fill="#fff"/><path d="M1 3 8 9l7-6" fill="none" stroke="#1f57ad" stroke-width="1.3"/></svg>
      </p>
      <p class="contact__row">www.tidewellconnect.com.au
        <svg class="contact__icon" viewBox="0 0 16 16" aria-hidden="true"><g fill="none" stroke="#fff" stroke-width="1.3"><circle cx="8" cy="8" r="6.5"/><ellipse cx="8" cy="8" rx="3" ry="6.5"/><path d="M1.5 8h13M2.5 4.5h11M2.5 11.5h11"/></g></svg>
      </p>
    </div>
  </section>

</main>
</body>
</html>
```